Talon Microsystems PowerPoint Master Slide Deck Design

This is a 2-phase project to design a slide deck for a semiconductor company in the Silicon Valley. The design budget will be increased with each phase.
The slide deck will need to have one version with a dark background for presentations and a second version with a white background. Otherwise, the slides will be the same. I anticipate we will need a total of 10 slides, but that number may change.
The first phase will be to design a Title and a Title and Content slide.
- The Title Slide is the first slide of the deck. It should include the presentation title, the presenter's name and date of presentation
- The Title and Content slide should include a title and content with bullet points and up to 2 additional sub-bullets
- The Title and Content slide should have a footer that includes the slide #, Talon Microsystems Confidential, and the logo. This footer will be on every slide except the Title Slide
The first two slides will serve as the format for the remaining ~8 slides:
-Header and Content Text (1, 2, 4 column)
-Header and Content Image (bar chart, pie chart, tables)
-Break
-Title only
-Closing (Talon logo only)
Our slides contain a lot of content so a clean and simple design is best.
Both phases will need to include pre-set color options for
-Text and Lines
-Shadows
-Bullets and sub-bullets (including shapes, ex. circle, slash, square, etc.)
-Bar charts, pie charts, tables
Samples of our collateral are attached. Logo files are also attached
Look and feel
Each slider illustrates characteristics of the customer's brand and the style your logo design should communicate.

```html
<!DOCTYPE html>
<html lang="en">
<head>
<meta charset="utf-8">
<title>Talon Microsystems Slide Master</title>
<link href="https://fonts.googleapis.com/css2?family=Montserrat:wght@400;500;600;700;800&display=swap" rel="stylesheet">
<style>
:root{
  --black:#000000;
  --ink:#0b0d12;
  --panel:#101216;
  --white:#ffffff;
  --cyan:#1ba8e0;
  --blue:#1a2fe0;
  --navy:#0a1f5c;
  --grey:#5c6470;
  --light:#f2f4f7;
}
*{margin:0;padding:0;box-sizing:border-box}
html,body{width:1200px;height:3992px;overflow:hidden;background:var(--white);font-family:'Montserrat',Arial,sans-serif}
.deck{position:relative;width:1200px;height:3992px}
.slide{position:absolute;left:0;width:1200px;height:656px;overflow:hidden;background:var(--black);color:var(--white)}
.s1{top:0}.s2{top:667px}.s3{top:1334px}.s4{top:2001px}.s5{top:2668px}.s6{top:3336px}
.brand{display:flex;align-items:center;gap:10px;font-weight:700;color:var(--white)}
.brand .dot{width:14px;height:14px;border-radius:50%;background:var(--cyan)}
.brand.dark{color:var(--ink)}
.s1 .brand{position:absolute;left:44px;top:40px;font-size:26px}
.s1 .photo{position:absolute;right:0;top:0;width:700px;height:656px}
.title-bar{position:absolute;left:0;height:50px;display:flex;align-items:center;padding-left:44px;font-weight:700;font-size:20px;border-radius:0 25px 25px 0}
.title-bar.main{top:196px;width:560px;background:var(--cyan)}
.title-bar.name{top:270px;width:430px;background:var(--blue)}
.title-bar.date{top:344px;width:460px;background:var(--cyan)}
.slide-title{position:absolute;left:64px;top:26px;font-size:26px;font-weight:700}
.footer{position:absolute;height:40px;background:var(--white);display:flex;align-items:center;color:var(--ink);font-size:11px;font-weight:600}
.footer .conf{flex:1}
.footer .brand{font-size:15px}
.footer .brand .dot{width:9px;height:9px}
.footer .num{width:40px;height:40px;background:var(--cyan);color:var(--white);display:flex;align-items:center;justify-content:center;font-size:13px;font-weight:700}
.footer.right{right:0;bottom:18px;width:620px;padding-left:40px}
.footer.right .brand{margin-right:60px}
.footer.left{left:0;bottom:18px;width:700px;padding-right:40px}
.footer.left .num{margin-right:30px}
.footer.left .brand{margin-left:40px}
.s2 .circuit{position:absolute;left:0;top:90px;width:1200px;height:470px}
.cards{position:absolute;left:64px;top:80px;width:1072px;display:flex;gap:20px}
.card{flex:1;height:450px;background:var(--white);color:var(--ink);padding:22px 22px}
.card.accent{background:var(--cyan);color:var(--white)}
.card h3{font-size:17px;font-weight:700;margin-bottom:10px}
.card p{font-size:9.5px;line-height:1.55;margin-bottom:20px}
.card ul{list-style:none}
.card li{position:relative;padding-left:20px;font-size:9.5px;line-height:1.55;margin-bottom:22px}
.card li::before{content:"";position:absolute;left:0;top:3px;width:10px;height:10px;border-radius:50%;background:var(--cyan)}
.card.accent li::before{background:var(--white)}
.s3{background:var(--white)}
.s3 .photo,.s5 .photo{position:absolute;left:0;top:0;width:640px;height:656px}
.s3 .panel,.s5 .panel{position:absolute;right:0;top:0;width:760px;height:656px}
.s3 .text{position:absolute;left:610px;top:86px;width:540px}
.s3 h2{font-size:26px;font-weight:700;margin-bottom:26px;line-height:1.25}
.body-copy p{font-size:10px;line-height:1.6;margin-bottom:14px}
.s4 .body-copy{position:absolute;left:64px;top:96px;width:1072px}
.s4 .body-copy p{font-size:10.5px;margin-bottom:16px}
.s5 .footer{left:0;top:0;width:520px;padding:0 24px}
.s5 h2{position:absolute;left:770px;top:300px;font-size:38px;font-weight:700}
.s6 .pattern{position:absolute;inset:0}
.s6 .brand{position:absolute;left:0;top:0;width:1200px;height:656px;justify-content:center;font-size:56px;gap:18px}
.s6 .brand .dot{width:32px;height:32px}
</style>
</head>
<body>
<main class="deck">

  <section class="slide s1">
    <svg class="photo" viewBox="0 0 700 656" role="img" aria-label="Blue circuit board photograph with a central processor chip">
      <defs>
        <linearGradient id="chipGlow" x1="0" y1="0" x2="1" y2="1">
          <stop offset="0" stop-color="#0a2a8a"/><stop offset="0.5" stop-color="#1b7fe0"/><stop offset="1" stop-color="#061540"/>
        </linearGradient>
      </defs>
      <path d="M200 0 H700 V656 H60 C150 560 120 450 210 360 C290 280 220 160 300 90 C330 60 260 30 200 0 Z" fill="url(#chipGlow)"/>
      <path d="M200 0 C260 30 330 60 300 90 C220 160 290 280 210 360 C120 450 150 560 60 656" fill="none" stroke="var(--cyan)" stroke-width="6"/>
    </svg>
    <div class="brand"><span class="dot"></span>Talon Microsystems</div>
    <div class="title-bar main">Lorem Ipsum&nbsp; Dolor Seit</div>
    <div class="title-bar name">Maren Holt</div>
    <div class="title-bar date">December 14 2023</div>
  </section>

  <section class="slide s2">
    <h2 class="slide-title">Sed ut perspiciatis unde omnis iste natus</h2>
    <svg class="circuit" viewBox="0 0 1200 470" role="img" aria-label="Dark blue circuit board texture">
      <defs><linearGradient id="boardBand" x1="0" y1="0" x2="1" y2="0"><stop offset="0" stop-color="#061a4a"/><stop offset="0.5" stop-color="#0b3a9a"/><stop offset="1" stop-color="#061a4a"/></linearGradient></defs>
      <rect width="1200" height="470" fill="url(#boardBand)"/>
    </svg>
    <div class="cards">
      <article class="card">
        <h3>Lorem Ipsum</h3>
        <p>Lorem ipsum dolor sit amet, consectetur adipiscing elit, sed do eiusmod tempor incididunt ut labore et dolore magna aliqua ut enim.</p>
        <ul>
          <li>Sed ut perspiciatis unde omnis iste natus error sit voluptatem accusantium doloremque laudantium, totam rem aperiam eaque ipsa quae ab illo inventore.</li>
          <li>Sed ut perspiciatis unde omnis iste natus error sit voluptatem accusantium doloremque laudantium, totam rem aperiam eaque ipsa quae ab illo inventore.</li>
          <li>Sed ut perspiciatis unde omnis iste natus error sit voluptatem accusantium doloremque laudantium.</li>
        </ul>
      </article>
      <article class="card accent">
        <h3>Lorem Ipsum</h3>
        <p>Lorem ipsum dolor sit amet, consectetur adipiscing elit, sed do eiusmod tempor incididunt ut labore et dolore magna aliqua ut enim.</p>
        <ul>
          <li>Sed ut perspiciatis unde omnis iste natus error sit voluptatem accusantium doloremque laudantium, totam rem aperiam eaque ipsa quae ab illo inventore.</li>
          <li>Sed ut perspiciatis unde omnis iste natus error sit voluptatem accusantium doloremque laudantium, totam rem aperiam eaque ipsa quae ab illo inventore.</li>
          <li>Sed ut perspiciatis unde omnis iste natus error sit voluptatem accusantium doloremque laudantium.</li>
        </ul>
      </article>
      <article class="card">
        <h3>Lorem Ipsum</h3>
        <p>Lorem ipsum dolor sit amet, consectetur adipiscing elit, sed do eiusmod tempor incididunt ut labore et dolore magna aliqua ut enim.</p>
        <ul>
          <li>Sed ut perspiciatis unde omnis iste natus error sit voluptatem accusantium doloremque laudantium, totam rem aperiam eaque ipsa quae ab illo inventore.</li>
          <li>Sed ut perspiciatis unde omnis iste natus error sit voluptatem accusantium doloremque laudantium, totam rem aperiam eaque ipsa quae ab illo inventore.</li>
          <li>Sed ut perspiciatis unde omnis iste natus error sit voluptatem accusantium doloremque laudantium.</li>
        </ul>
      </article>
    </div>
    <footer class="footer right"><span class="conf">Talon Microsystems Confidential</span><span class="brand dark"><span class="dot"></span>Talon</span><span class="num">02</span></footer>
  </section>

  <section class="slide s3">
    <svg class="photo" viewBox="0 0 640 656" role="img" aria-label="Close-up of a circuit board seen through a magnifying glass">
      <defs><radialGradient id="lensTone" cx="0.45" cy="0.5" r="0.7"><stop offset="0" stop-color="#6a5a8a"/><stop offset="0.6" stop-color="#2a2f55"/><stop offset="1" stop-color="#12142a"/></radialGradient></defs>
      <rect width="640" height="656" fill="url(#lensTone)"/>
    </svg>
    <svg class="panel" viewBox="0 0 760 656" aria-hidden="true">
      <path d="M240 0 H760 V656 H150 C230 540 200 420 160 330 C120 230 170 90 240 0 Z" fill="var(--black)"/>
      <path d="M240 0 C170 90 120 230 160 330 C200 420 230 540 150 656" fill="none" stroke="var(--white)" stroke-width="3"/>
    </svg>
    <div class="text">
      <h2>Lorem ipsum dolor sit amet, consectetur</h2>
      <div class="body-copy">
        <p>Sed ut perspiciatis unde omnis iste natus error sit voluptatem accusantium doloremque laudantium, totam rem aperiam, eaque ipsa quae ab illo inventore veritatis et quasi architecto beatae vitae dicta sunt explicabo. Nemo enim ipsam voluptatem quia voluptas sit aspernatur aut odit aut fugit.</p>
        <p>Neque porro quisquam est, qui dolorem ipsum quia dolor sit amet, consectetur, adipisci velit, sed quia non numquam eius modi tempora incidunt ut labore et dolore magnam aliquam quaerat voluptatem.</p>
        <p>Lorem ipsum dolor sit amet, consectetur adipiscing elit, sed do eiusmod tempor incididunt ut labore et dolore magna aliqua. Ut enim ad minim veniam, quis nostrud exercitation ullamco laboris nisi ut aliquip ex ea commodo consequat.</p>
        <p>Ut enim ad minima veniam, quis nostrum exercitationem ullam corporis suscipit laboriosam, nisi ut aliquid ex ea commodi consequatur.</p>
      </div>
    </div>
    <footer class="footer left"><span class="num">03</span><span class="conf">Talon Microsystems Confidential</span><span class="brand dark"><span class="dot"></span>Talon</span></footer>
  </section>

  <section class="slide s4">
    <h2 class="slide-title">Sed ut perspiciatis unde omnis iste natus</h2>
    <div class="body-copy">
      <p>Lorem ipsum dolor sit amet, consectetur adipiscing elit, sed do eiusmod tempor incididunt ut labore et dolore magna aliqua. Ut enim ad minim veniam, quis nostrud exercitation ullamco laboris nisi ut aliquip ex ea commodo consequat. Duis aute irure dolor in reprehenderit in voluptate velit esse cillum dolore eu fugiat nulla pariatur. Excepteur sint occaecat cupidatat non proident, sunt in culpa qui officia deserunt mollit anim id est laborum.</p>
      <p>Sed ut perspiciatis unde omnis iste natus error sit voluptatem accusantium doloremque laudantium, totam rem aperiam, eaque ipsa quae ab illo inventore veritatis et quasi architecto beatae vitae dicta sunt explicabo. Nemo enim ipsam voluptatem quia voluptas sit aspernatur aut odit aut fugit, sed quia consequuntur magni dolores eos qui ratione voluptatem sequi nesciunt.</p>
      <p>Neque porro quisquam est, qui dolorem ipsum quia dolor sit amet, consectetur, adipisci velit, sed quia non numquam eius modi tempora incidunt ut labore et dolore magnam aliquam quaerat voluptatem. Ut enim ad minima veniam, quis nostrum exercitationem ullam corporis suscipit laboriosam, nisi ut aliquid ex ea commodi consequatur.</p>
      <p>Lorem ipsum dolor sit amet, consectetur adipiscing elit, sed do eiusmod tempor incididunt ut labore et dolore magna aliqua. Ut enim ad minim veniam, quis nostrud exercitation ullamco laboris nisi ut aliquip ex ea commodo consequat. Duis aute irure dolor in reprehenderit in voluptate velit esse cillum dolore eu fugiat nulla pariatur.</p>
      <p>Sed ut perspiciatis unde omnis iste natus error sit voluptatem accusantium doloremque laudantium, totam rem aperiam, eaque ipsa quae ab illo inventore veritatis et quasi architecto beatae vitae dicta sunt explicabo. Nemo enim ipsam voluptatem quia voluptas sit aspernatur aut odit aut fugit.</p>
    </div>
    <footer class="footer right"><span class="conf">Talon Microsystems Confidential</span><span class="brand dark"><span class="dot"></span>Talon</span><span class="num">04</span></footer>
  </section>

  <section class="slide s5">
    <svg class="photo" viewBox="0 0 640 656" role="img" aria-label="Blue and amber circuit board photograph">
      <defs><linearGradient id="boardWarm" x1="0" y1="0" x2="1" y2="1"><stop offset="0" stop-color="#1a4fb0"/><stop offset="0.55" stop-color="#0c2a6a"/><stop offset="1" stop-color="#7a4a1a"/></linearGradient></defs>
      <rect width="640" height="656" fill="url(#boardWarm)"/>
    </svg>
    <svg class="panel" viewBox="0 0 760 656" aria-hidden="true">
      <path d="M240 0 H760 V656 H150 C230 540 200 420 160 330 C120 230 170 90 240 0 Z" fill="var(--panel)"/>
      <path d="M240 0 C170 90 120 230 160 330 C200 420 230 540 150 656" fill="none" stroke="var(--white)" stroke-width="3"/>
    </svg>
    <footer class="footer"><span class="conf">Talon Microsystems Confidential</span><span class="brand dark"><span class="dot"></span>Talon</span></footer>
    <h2>Talon Microsystems</h2>
  </section>

  <section class="slide s6">
    <svg class="pattern" viewBox="0 0 1200 656" role="img" aria-label="Faint dark circuit trace background">
      <defs><radialGradient id="closingGlow" cx="0.5" cy="0.5" r="0.7"><stop offset="0" stop-color="#1a2030"/><stop offset="1" stop-color="#05070b"/></radialGradient></defs>
      <rect width="1200" height="656" fill="url(#closingGlow)"/>
    </svg>
    <div class="brand"><span class="dot"></span>Talon Microsystems</div>
  </section>

</main>
</body>
</html>
```